Business card for Luxury Portable Restroom Trailer company

We are a Luxury Portable Restroom Trailer Company Called FALCRIDGE HIRES. Based in Orange County California. We provide portable restroom trailers for events, such as, Weddings, Concerts, Charity events, Sporting events, Tournaments, Corporate events, ect. We rent and Sell the Luxury restrooms. Our colors are white, grey, and Orange. As you will see in the logo we uploaded.
There are 2 people in the company so the names and titles will change for the 3 people but card will remain the same. Here is the information for each Person: Dwight Penner CFO 555 318-0476
next Person: Leon Marchetti VP 555 318-0476
Next Person: Owen Marchetti CEO 555 318-0476
Information to include on the card: Luxury Restroom Trailers Rental and Sales. Weddings, Concerts, Charity, Sporting and Corp. Events.

```html
<!DOCTYPE html>
<html lang="en">
<head>
<meta charset="utf-8">
<title>Falcridge Hires – Business Card</title>
<link rel="stylesheet" href="https://fonts.googleapis.com/css2?family=Montserrat:wght@400;600;700;800&display=swap">
<style>
  :root {
    --bg: #1e1e1f;
    --orange: #ec6a1f;
    --grey-text: #4d4d4f;
    --card-white: #ffffff;
    --card-grey: #4b4b4d;
    --pattern-grey: #454547;
  }
  * { box-sizing: border-box; margin: 0; padding: 0; }
  html, body { width: 1200px; height: 878px; overflow: hidden; }
  body {
    background: var(--bg);
    font-family: "Montserrat", Arial, sans-serif;
    position: relative;
  }
  .card {
    position: absolute;
    left: 260px;
    width: 680px;
    height: 388px;
    overflow: hidden;
  }
  /* back side */
  .card-back { top: 34px; background: var(--card-grey); }
  .back-pattern {
    position: absolute; inset: 0;
    background: radial-gradient(circle at 40% 50%, var(--pattern-grey), var(--card-grey));
  }
  .back-mark {
    position: absolute; right: 70px; top: 118px;
    display: flex; flex-direction: column; align-items: center; gap: 10px;
  }
  .back-ring {
    width: 64px; height: 64px; border-radius: 50%;
    border: 4px solid var(--orange);
  }
  .back-name {
    color: var(--orange); font-weight: 800; font-size: 14px; letter-spacing: 1px;
  }
  /* front side */
  .card-front { top: 456px; background: var(--card-white); }
  .brand-name {
    position: absolute; top: 52px; left: 0; right: 0;
    text-align: center;
    color: var(--orange); font-weight: 800; font-size: 46px; letter-spacing: 2px;
  }
  .person {
    position: absolute; top: 170px; right: 372px; text-align: right;
  }
  .person-name {
    color: var(--orange); font-weight: 800; font-size: 26px; letter-spacing: 1px;
    white-space: nowrap;
  }
  .person-title {
    color: var(--grey-text); font-size: 15px; letter-spacing: 1px; margin-top: 6px;
  }
  .divider {
    position: absolute; left: 330px; top: 162px; width: 1.5px; height: 64px;
    background: var(--orange);
  }
  .contacts {
    position: absolute; left: 348px; top: 158px;
    list-style: none;
  }
  .contacts li {
    display: flex; align-items: center; gap: 9px;
    color: var(--grey-text); font-size: 15px; letter-spacing: 0.6px;
    height: 24px;
  }
  .contacts svg { width: 12px; height: 12px; flex: none; }
  .tagline {
    position: absolute; top: 264px; left: 0; right: 0; text-align: center;
    color: var(--orange); font-weight: 700; font-size: 16px; letter-spacing: 0.6px;
  }
  .events {
    position: absolute; top: 292px; left: 0; right: 0; text-align: center;
    color: var(--grey-text); font-size: 18px; letter-spacing: 0.6px;
  }
</style>
</head>
<body>

<section class="card card-back">
  <div class="back-pattern" role="img" aria-label="Tone-on-tone repeating pattern of the brand emblem"></div>
  <div class="back-mark">
    <div class="back-ring"></div>
    <div class="back-name">FALCRIDGE HIRES</div>
  </div>
</section>

<section class="card card-front">
  <div class="brand-name">FALCRIDGE HIRES</div>

  <div class="person">
    <div class="person-name">OWEN MARCHETTI</div>
    <div class="person-title">CEO</div>
  </div>

  <div class="divider"></div>

  <ul class="contacts">
    <li>
      <svg viewBox="0 0 12 12" aria-hidden="true"><path fill="#ec6a1f" d="M2.5 1 L4.5 1 L5 3.5 L3.8 4.4 Q4.8 6.8 7.6 8.2 L8.5 7 L11 7.5 L11 9.5 Q10.5 11 9 11 Q2 10 1 3 Q1 1.5 2.5 1 Z"/></svg>
      555 318-0476
    </li>
    <li>
      <svg viewBox="0 0 12 12" aria-hidden="true"><rect x="0.5" y="2.5" width="11" height="7.5" fill="#ec6a1f"/><path d="M0.8 2.8 L6 7 L11.2 2.8" stroke="#fff" stroke-width="1" fill="none"/></svg>
      owen@falcridgehires.com
    </li>
    <li>
      <svg viewBox="0 0 12 12" aria-hidden="true"><circle cx="6" cy="6" r="5.5" fill="#ec6a1f"/><path d="M0.5 6 H11.5 M6 0.5 Q3 6 6 11.5 M6 0.5 Q9 6 6 11.5" stroke="#fff" stroke-width="0.8" fill="none"/></svg>
      www.falcridgehires.com
    </li>
  </ul>

  <p class="tagline">Luxury Restroom Trailers Rental and Sales</p>
  <p class="events">Weddings | Concerts | Charity | Sporting | Corp</p>
</section>

</body>
</html>
```